Allied Health team of Physiotherapists & Occupational Therapists seek a business card design

We have our new logo, we now need our new business cards and stationary. Tidewell: Oedema & Family Clinic is seeking a generic card design to represent our whole team and individual cards for each therapist that incorporates our new logo to communicate our holistic approach that is calming, nuturing, supportive and welcoming.
Our Physiotherapists and Occupational Therapists assess, treat and provide education for people who are at risk of or who have lymphoedema. This is often as a result of treatment for cancer. We provide pre-operative and post-operative management and cancer rehabilitation in our Pilates studio. Our team also consists of Physiotherapists who have a strong interest in pelvic floor and continence management for both men and women.

Target Market(s)

Mainly women health conscious

Industry/Entity Type

Allied Health: Physiotherapy / Occupational Therapy

Contact Information for Business Card

Address: 14 Gallivant Ave Frankston 3199 Phone: 84316570 fax: 8431 6578 Email: info@tidewellcareservices.com.au Website: tidewellcareservices.com.au Facebook address: facebook.com/TidewellOedemaAndFamilyCareClinic. Room to write appointments. Individual cards need to have name, office email and individual email and professional details

Requirements
Must have
• Logo as per uploaded documents

```html
<!DOCTYPE html>
<html lang="en">
<head>
<meta charset="utf-8">
<title>Tidewell: Oedema &amp; Family Clinic — Business Cards</title>
<link rel="stylesheet" href="https://fonts.googleapis.com/css2?family=Arimo:wght@400;700&family=Cinzel:wght@400&display=swap">
<style>
  :root {
    --backdrop: #141414;
    --card: #262627;
    --card-edge: #d9926a;
    --copper: #e39e72;
    --ink-light: #f2f2f2;
    --emboss: #3a3a3c;
    --emboss-line: #454548;
  }
  * { box-sizing: border-box; margin: 0; padding: 0; }
  html, body {
    width: 1200px; height: 820px; overflow: hidden;
    background: var(--backdrop);
  }
  .canvas {
    width: 1200px; height: 820px;
    display: flex; align-items: center; justify-content: center; gap: 40px;
  }
  .card {
    position: relative;
    width: 540px; height: 330px;
    background: var(--card);
    border-bottom: 4px solid var(--card-edge);
    border-right: 2px solid var(--card-edge);
    box-shadow: 0 18px 40px rgba(0,0,0,.6);
  }
  /* front */
  .card-front { padding: 34px 30px 0 34px; font-family: "Arimo", Arial, sans-serif; color: var(--ink-light); }
  .therapist-name {
    font-family: "Cinzel", Georgia, serif;
    color: var(--copper); font-size: 24px; letter-spacing: 2px; font-weight: 400;
    margin-bottom: 6px;
  }
  .qualifications { font-size: 12.5px; line-height: 1.4; }
  .specialties { margin-top: 14px; font-size: 13.5px; font-weight: 700; line-height: 1.3; }
  .contact-list { list-style: none; margin-top: 30px; font-size: 13px; line-height: 1.55; }
  .contact-list li { display: flex; align-items: center; gap: 9px; }
  .contact-icon { width: 14px; height: 14px; flex: none; }
  .clinic-seal {
    position: absolute; right: 28px; top: 120px;
    width: 150px; height: 150px;
    border: 1.5px solid var(--copper); border-radius: 50%;
    display: flex; align-items: center; justify-content: center; text-align: center;
    padding: 18px;
    font-family: "Arimo", Arial, sans-serif; font-weight: 400;
    color: var(--copper); font-size: 14px; line-height: 1.35;
  }
  /* back */
  .card-back { display: flex; align-items: center; justify-content: center; }
  .clinic-seal-emboss {
    width: 190px; height: 190px;
    border: 1.5px solid var(--emboss-line); border-radius: 50%;
    display: flex; align-items: center; justify-content: center; text-align: center;
    padding: 24px;
    font-family: "Arimo", Arial, sans-serif; font-weight: 400;
    color: var(--emboss); font-size: 17px; line-height: 1.35;
  }
</style>
</head>
<body>
<main class="canvas">
  <section class="card card-front" aria-label="Card front">
    <h1 class="therapist-name">MAREN ASHBY</h1>
    <p class="qualifications">
      B. Physio (Hons), B.App.Sci.(Human Movement/Psych)<br>
      Post Grad Certif. Exercise for Women<br>
      Post Grad Certif. Continence &amp; Pelvic Floor Rehabilitation
    </p>
    <p class="specialties">
      Physiotherapist<br>
      Lymphoedema &amp; Oncology Rehabilitation<br>
      Continence &amp; Pelvic Floor
    </p>
    <ul class="contact-list">
      <li>
        <svg class="contact-icon" viewBox="0 0 16 16" aria-hidden="true"><path d="M3.5 1.5l2.5 3-1.5 1.5c.8 2 2.5 3.7 4.5 4.5L10.5 9l3 2.5-1.5 2.5C7 14 2 9 2 3z" fill="var(--copper)"/></svg>
        000 4444 5555
      </li>
      <li>
        <svg class="contact-icon" viewBox="0 0 16 16" aria-hidden="true"><rect x="1" y="3.5" width="14" height="9" fill="var(--copper)"/><path d="M1 3.5l7 5 7-5" stroke="var(--card)" stroke-width="1.2" fill="none"/></svg>
        info@tidewellcareservices.com.au
      </li>
      <li>
        <svg class="contact-icon" viewBox="0 0 16 16" aria-hidden="true"><rect x="1" y="3.5" width="14" height="9" fill="var(--copper)"/><path d="M1 3.5l7 5 7-5" stroke="var(--card)" stroke-width="1.2" fill="none"/></svg>
        name@tidewellcareservices.com.au
      </li>
      <li>
        <svg class="contact-icon" viewBox="0 0 16 16" aria-hidden="true"><g fill="none" stroke="var(--copper)" stroke-width="1.3"><circle cx="8" cy="8" r="6.3"/><ellipse cx="8" cy="8" rx="2.8" ry="6.3"/><path d="M1.7 8h12.6M2.8 4.8h10.4M2.8 11.2h10.4"/></g></svg>
        www.tidewellcareservices.com.au
      </li>
    </ul>
    <div class="clinic-seal">Tidewell: Oedema &amp; Family Clinic</div>
  </section>

  <section class="card card-back" aria-label="Card back">
    <div class="clinic-seal-emboss">Tidewell: Oedema &amp; Family Clinic</div>
  </section>
</main>
</body>
</html>
```